Talvoro bonds (Surety bond broker)

We are a broker of surety bonds, we need a presentation and a flyer with fresh design. Our core values are reliable, on time and customized service. We want to transmit to our clients, they can leave on us the process of underwriting and issuing a surety bond, so they can focus on their business with no distractions.

Font styles to use
Sans Serif
Other font styles liked:

Requirements
Must have
• Visually attractive.
Main Message: Fast service issuing and underwriting surety bonds, reliable, nos surprises, we are always one step ahead, customized and personalized bonding solutions.
Nice to have
• Have short version for the flyer, and extended version for the presentation.
Should not have
• We already have a logo (attached), maintain colors

```html
<!DOCTYPE html>
<html lang="es">
<head>
<meta charset="utf-8">
<title>Talvoro — Contacto</title>
<link href="https://fonts.googleapis.com/css2?family=Catamaran:wght@500;600&family=Kreon:wght@300;400;500&family=Lato:wght@300&display=swap" rel="stylesheet">
<style>
  :root {
    --green: #6aab44;
    --ink: #1f1f1f;
    --white: #ffffff;
    --grey: #5b5b5b;
  }
  html, body { margin: 0; padding: 0; overflow: hidden; background: var(--white); }
  .card {
    position: relative; width: 1200px; height: 848px; overflow: hidden;
    background: var(--ink);
  }
  .backdrop { position: absolute; inset: 0; }
  .title {
    position: absolute; left: 89px; top: 80px; margin: 0;
    font-family: "Catamaran", sans-serif; font-weight: 600; font-size: 80px;
    color: var(--green); letter-spacing: -1px; line-height: 1;
  }
  .contact { position: absolute; width: 398px; }
  .contact-name {
    display: flex; align-items: flex-end; gap: 12px;
    padding-bottom: 5px; border-bottom: 3px solid var(--green);
    font-family: "Kreon", serif; font-weight: 500; font-size: 36px;
    color: var(--green); line-height: 1;
  }
  .contact-name svg { width: 40px; height: 42px; flex: none; }
  .contact-row {
    display: flex; align-items: center; gap: 20px; margin-top: 12px;
    color: var(--white); line-height: 1; padding-left: 6px;
  }
  .contact-row svg { width: 30px; height: 30px; flex: none; }
  .phone { font-family: "Lato", sans-serif; font-weight: 300; font-size: 31px; letter-spacing: -0.5px; }
  .email { font-family: "Kreon", serif; font-weight: 300; font-size: 33px; }
  .brand {
    position: absolute; right: 30px; top: 682px; margin: 0;
    font-family: "Catamaran", sans-serif; font-weight: 500; font-size: 78px;
    color: var(--green); letter-spacing: 2px; line-height: 1;
  }
  .tagline {
    position: absolute; right: 58px; top: 758px;
    font-family: "Catamaran", sans-serif; font-weight: 500; font-size: 19px;
    color: var(--ink); letter-spacing: 1.5px; line-height: 1;
  }
  .website {
    position: absolute; right: 112px; top: 782px;
    font-family: "Kreon", serif; font-weight: 300; font-size: 29px;
    color: var(--grey); line-height: 1;
  }
</style>
</head>
<body>
<main class="card">
  <svg class="backdrop" viewBox="0 0 1200 848" width="1200" height="848" aria-hidden="true">
    <defs>
      <linearGradient id="night" x1="0" y1="0" x2="1" y2="1">
        <stop offset="0" stop-color="#1c1c1c"/>
        <stop offset="0.55" stop-color="#2c2c2c"/>
        <stop offset="1" stop-color="#1e1e1e"/>
      </linearGradient>
    </defs>
    <rect width="1200" height="848" fill="url(#night)" role="img" aria-label="Dark photograph of an old wooden house at dusk"/>
    <path class="sweep-white" d="M0,700 C420,650 900,520 1200,278 L1200,848 L0,848 Z" fill="var(--white)"/>
    <path class="sweep-dark" d="M0,738 C450,690 860,580 1100,405 C860,610 460,790 150,848 L0,848 Z" fill="var(--ink)"/>
    <path class="sweep-green" d="M150,848 C520,780 920,630 1200,330 L1200,378 C940,650 620,800 320,848 Z" fill="var(--green)"/>
    <path class="sweep-green-thin" d="M767,694 C960,640 1110,520 1200,400 L1200,414 C1110,560 960,665 767,694 Z" fill="var(--green)"/>
  </svg>

  <h1 class="title">Contacto</h1>

  <svg width="0" height="0" style="position:absolute">
    <symbol id="icon-person" viewBox="0 0 40 42"><circle cx="20" cy="12" r="10" fill="var(--green)"/><path d="M2,42 C2,30 9,25 20,25 C31,25 38,30 38,42 Z" fill="var(--green)"/></symbol>
    <symbol id="icon-phone" viewBox="0 0 30 30"><rect x="8" y="1" width="14" height="28" rx="3" fill="none" stroke="var(--green)" stroke-width="2.5"/><line x1="12" y1="5" x2="18" y2="5" stroke="var(--green)" stroke-width="2"/><circle cx="15" cy="24.5" r="1.6" fill="var(--green)"/></symbol>
    <symbol id="icon-mail" viewBox="0 0 30 30"><rect x="1" y="7" width="28" height="17" fill="var(--green)"/><path d="M1,7 L15,17 L29,7 M1,24 L12,15 M29,24 L18,15" fill="none" stroke="var(--ink)" stroke-width="1.6"/></symbol>
  </svg>

  <section class="contact" style="left:80px; top:232px;">
    <div class="contact-name"><svg><use href="#icon-person"/></svg>Marta Lozano</div>
    <div class="contact-row phone"><svg><use href="#icon-phone"/></svg>55 1834 7620</div>
    <div class="contact-row email"><svg><use href="#icon-mail"/></svg>mlozano@talvoro.com</div>
  </section>

  <section class="contact" style="left:607px; top:229px;">
    <div class="contact-name"><svg><use href="#icon-person"/></svg>Irene Vidal</div>
    <div class="contact-row phone"><svg><use href="#icon-phone"/></svg>55 4712 0951</div>
    <div class="contact-row email"><svg><use href="#icon-mail"/></svg>ividal@talvoro.com</div>
  </section>

  <section class="contact" style="left:80px; top:417px;">
    <div class="contact-name"><svg><use href="#icon-person"/></svg>Rodrigo Salcedo</div>
    <div class="contact-row phone"><svg><use href="#icon-phone"/></svg>55 2168 3075</div>
    <div class="contact-row email"><svg><use href="#icon-mail"/></svg>rsalcedo@talvoro.com</div>
  </section>

  <p class="brand">TALVORO</p>
  <div class="tagline">SECURING CLIENTS</div>
  <div class="website">www.talvoro.com</div>
</main>
</body>
</html>
```